Business Card Design

I need a business card for a new company based in Australia called "MedLinkora".

Its a cloud program for GPs that allows them to search for the specialist they require using a simple user friendly tool.

I would like the colours to match those in the program (the colours in the logo attached).

The final design should reflect the programs clarity, ease of use and professionalism.

Target Market(s)

GPs and other Health Professionals

Industry/Entity Type

Business

Contact Information for Business Card

MedLinkora; The Whole Consultant Index; Marla Voss CEO; 0438215967; marla@medlinkora.example; www.medlinkora.example

Requirements
Must have
• Must have the logo attached; the web address and my name and phone number
Nice to have
• the slogan "The Whole Consultant Index"

```html
<!DOCTYPE html>
<html lang="en">
<head>
<meta charset="utf-8">
<title>MedLinkora Business Card</title>
<link href="https://fonts.googleapis.com/css2?family=Open+Sans:wght@400;600;700&display=swap" rel="stylesheet">
<style>
  :root {
    --brand-blue: #1aaee6;
    --ink-grey: #6d6e71;
    --ink-dark: #2b2b2b;
    --band-grey: #c9cacc;
    --paper: #ffffff;
    --backdrop: #eef0f2;
  }
  * { margin: 0; padding: 0; box-sizing: border-box; }
  html, body {
    width: 1200px; height: 829px; overflow: hidden;
    background: var(--backdrop);
    font-family: "Open Sans", Arial, sans-serif;
  }
  .canvas { position: relative; width: 1200px; height: 829px; }
  .card {
    position: absolute; width: 530px; height: 324px;
    top: 252px; overflow: hidden;
    box-shadow: 0 6px 18px rgba(0,0,0,0.12);
  }
  /* Front */
  .card-front { left: 45px; background: var(--paper); }
  .front-corner-band {
    position: absolute; left: 0; top: 0; width: 235px; height: 10px;
    background: var(--band-grey);
  }
  .brand-block { position: absolute; left: 34px; top: 116px; }
  .brand-name {
    font-size: 42px; font-weight: 400; color: var(--brand-blue);
    letter-spacing: -1px; line-height: 1; white-space: nowrap;
  }
  .brand-tagline {
    margin-top: 5px; font-size: 14px; color: var(--ink-grey);
    letter-spacing: 0.3px; white-space: nowrap;
  }
  .contact-list {
    position: absolute; right: 26px; top: 36px; list-style: none;
    text-align: right; font-size: 14px; color: var(--ink-dark);
  }
  .contact-list li {
    display: flex; align-items: center; justify-content: flex-end;
    gap: 7px; margin-bottom: 22px; white-space: nowrap;
  }
  .contact-list li:last-child { margin-bottom: 0; }
  .contact-icon { width: 14px; height: 14px; flex: none; }
  .web-band {
    position: absolute; right: 0; top: 122px; width: 218px; height: 34px;
    background: var(--brand-blue);
    color: var(--paper); font-size: 14px; letter-spacing: 1.1px;
    display: flex; align-items: center; justify-content: center;
    white-space: nowrap;
  }
  .person { position: absolute; left: 34px; top: 236px; }
  .person-name { font-size: 18px; font-weight: 700; color: var(--brand-blue); }
  .person-role { font-size: 15px; color: var(--ink-grey); margin-top: 2px; }
  /* Back */
  .card-back {
    left: 625px; background: var(--brand-blue);
    color: var(--paper); text-align: center;
  }
  .back-brand { position: absolute; left: 0; right: 0; top: 92px; }
  .back-brand .brand-name { color: var(--paper); font-size: 60px; }
  .back-brand .brand-tagline { color: var(--paper); font-size: 17px; }
  .back-web {
    position: absolute; left: 0; right: 0; top: 232px;
    font-size: 17px; letter-spacing: 1.6px;
  }
</style>
</head>
<body>
<main class="canvas">
  <section class="card card-front" aria-label="Business card front">
    <div class="front-corner-band"></div>
    <ul class="contact-list">
      <li>
        <svg class="contact-icon" viewBox="0 0 16 16" aria-hidden="true">
          <circle cx="8" cy="8" r="7.2" fill="none" stroke="var(--brand-blue)" stroke-width="1.4"/>
          <path d="M5.6 4.4l1.3 1.6-.8 1c.5 1 1.3 1.8 2.3 2.3l1-.8 1.6 1.3-.9 1.3c-2.8-.5-5-2.7-5.5-5.5z" fill="var(--brand-blue)"/>
        </svg>
        <span>0438215967</span>
      </li>
      <li>
        <svg class="contact-icon" viewBox="0 0 16 16" aria-hidden="true">
          <path d="M1.5 6.5L8 2l6.5 4.5V14h-13z" fill="var(--brand-blue)"/>
          <path d="M1.5 6.5L8 10.5l6.5-4" fill="none" stroke="var(--paper)" stroke-width="1.2"/>
        </svg>
        <span>marla@medlinkora.example</span>
      </li>
    </ul>
    <div class="web-band">www.medlinkora.example</div>
    <div class="brand-block">
      <div class="brand-name">MedLinkora</div>
      <div class="brand-tagline">The Whole Consultant Index</div>
    </div>
    <div class="person">
      <div class="person-name">Marla Voss</div>
      <div class="person-role">CEO</div>
    </div>
  </section>

  <section class="card card-back" aria-label="Business card back">
    <div class="back-brand">
      <div class="brand-name">MedLinkora</div>
      <div class="brand-tagline">The Whole Consultant Index</div>
    </div>
    <div class="back-web">www.medlinkora.example</div>
  </section>
</main>
</body>
</html>
```